Presentation Folder with inside Pockets

We need a Presentation Folder with inside pockets. The size of the folder will be 9" x 12" and will be printed on the cover, the back and the inside folder flaps. The design will be very simple and consist of our logo (large) on the front cover and our logo (smaller) and contact information on the back. We are open to various colors that you think may go along with our logo. When you display your work, show the front, back and inside.

Target Market(s)

Pharmaceutical Companies

Industry/Entity Type

Work

Requirements
Should not have
• please do not add stock medical photos.

```html
<!DOCTYPE html>
<html lang="en">
<head>
<meta charset="utf-8">
<title>Meridian Trials Co. – Presentation Folder</title>
<link rel="stylesheet" href="https://fonts.googleapis.com/css2?family=Michroma&family=Source+Sans+3:wght@400;600&display=swap">
<style>
:root{
  --stage:#000000;
  --blue-light:#1b8fd0;
  --blue-mid:#176aa6;
  --blue-deep:#0f3f6b;
  --green-light:#a6cf3c;
  --green-mid:#7fb536;
  --green-deep:#4f8f2e;
  --wave-blue:#1f7fc4;
  --pocket-light:#fafafa;
  --pocket-shade:#d9d9d9;
  --ink:#1b1b1b;
  --white:#ffffff;
  --card-line:#8a8a8a;
  --accent-orange:#f08a1c;
}
*{margin:0;padding:0;box-sizing:border-box}
html,body{width:1200px;height:1007px;overflow:hidden;background:var(--stage)}
.folder{position:relative;width:1200px;height:1007px}
.folder-art{position:absolute;inset:0}
.brand{position:absolute;font-family:"Michroma",sans-serif;line-height:1.05;display:flex;align-items:center;gap:12px}
.brand-dot{border-radius:50%;flex:none}
.brand-name span{display:block;text-align:center}
.back-brand{left:116px;top:588px;color:var(--white);font-size:19px}
.back-brand .brand-dot{width:52px;height:52px;background:var(--accent-orange)}
.front-brand{left:674px;top:232px;color:var(--ink);font-size:21px}
.front-brand .brand-dot{width:60px;height:60px;background:var(--accent-orange)}
.back-contact{position:absolute;left:116px;top:674px;color:var(--white);font-family:"Source Sans 3",sans-serif;font-size:13px;line-height:22px}
.back-contact .row{display:flex;align-items:center;gap:6px}
.back-contact svg{flex:none}
.web-address{position:absolute;right:92px;top:699px;color:var(--white);font-family:"Source Sans 3",sans-serif;font-size:13px;letter-spacing:2.5px}
.web-address b{font-weight:600}
.card{position:absolute;width:199px;height:113px;background:var(--white);border:1px solid var(--card-line);font-family:"Source Sans 3",sans-serif;color:var(--ink)}
.card-left{left:229px;top:793px}
.card-right{left:780px;top:793px}
.card-brand{position:absolute;left:10px;top:14px;display:flex;align-items:center;gap:5px;font-family:"Michroma",sans-serif;font-size:7.5px;line-height:1}
.card-brand .brand-dot{width:14px;height:14px;background:var(--accent-orange)}
.card-contact{position:absolute;left:12px;top:64px;font-size:5.5px;line-height:8px}
.card-address{position:absolute;left:12px;top:90px;font-size:5.5px;line-height:7px}
.card-holder{position:absolute;right:18px;top:68px;font-size:6.5px;font-weight:600;line-height:8px;text-align:center}
</style>
</head>
<body>
<main class="folder">
  <svg class="folder-art" width="1200" height="1007" viewBox="0 0 1200 1007" aria-hidden="true">
    <defs>
      <radialGradient id="backCoverFill" cx="0.4" cy="0.3" r="0.85">
        <stop offset="0" stop-color="var(--blue-light)"/>
        <stop offset="0.55" stop-color="var(--blue-mid)"/>
        <stop offset="1" stop-color="var(--blue-deep)"/>
      </radialGradient>
      <radialGradient id="frontCoverFill" cx="0.65" cy="0.35" r="0.8">
        <stop offset="0" stop-color="var(--green-light)"/>
        <stop offset="0.6" stop-color="var(--green-mid)"/>
        <stop offset="1" stop-color="var(--green-deep)"/>
      </radialGradient>
      <linearGradient id="pocketFill" x1="0" y1="0" x2="0" y2="1">
        <stop offset="0" stop-color="var(--pocket-shade)"/>
        <stop offset="0.5" stop-color="var(--pocket-light)"/>
        <stop offset="1" stop-color="var(--pocket-shade)"/>
      </linearGradient>
    </defs>

    <!-- back cover -->
    <rect class="back-cover" x="96" y="51" width="507" height="680" fill="url(#backCoverFill)"/>
    <circle class="back-accent-circle" cx="240" cy="195" r="118" fill="var(--white)" opacity="0.12"/>

    <!-- front cover -->
    <rect class="front-cover" x="603" y="51" width="510" height="680" fill="url(#frontCoverFill)"/>
    <path class="front-wave-shadow" d="M603 51 L672 51 C630 180 615 260 650 420 C680 560 698 640 690 731 L603 731 Z" fill="var(--green-deep)" opacity="0.45"/>
    <path class="front-wave-line" d="M672 51 C630 180 615 260 650 420 C680 560 698 640 690 731" fill="none" stroke="var(--wave-blue)" stroke-width="4"/>
    <circle class="front-accent-circle" cx="992" cy="550" r="110" fill="var(--white)" opacity="0.14"/>

    <!-- inside pockets -->
    <path class="pocket-left" d="M52 751 L96 733 L600 733 L596 958 L72 958 Q60 958 60 946 Z" fill="url(#pocketFill)"/>
    <path class="pocket-right" d="M1160 751 L1113 733 L608 733 L612 958 L1142 958 Q1154 958 1154 946 Z" fill="url(#pocketFill)"/>

    <!-- card slits -->
    <g class="card-slits" stroke="var(--card-line)" stroke-width="1">
      <line x1="221" y1="785" x2="244" y2="805"/><line x1="436" y1="785" x2="413" y2="805"/>
      <line x1="221" y1="914" x2="244" y2="894"/><line x1="436" y1="914" x2="413" y2="894"/>
      <line x1="772" y1="785" x2="795" y2="805"/><line x1="987" y1="785" x2="964" y2="805"/>
      <line x1="772" y1="914" x2="795" y2="894"/><line x1="987" y1="914" x2="964" y2="894"/>
    </g>
  </svg>

  <div class="brand back-brand">
    <span class="brand-dot"></span>
    <div class="brand-name"><span>MERIDIAN TRIALS</span><span>CO.</span></div>
  </div>

  <div class="back-contact">
    <div class="row">
      <svg width="12" height="12" viewBox="0 0 12 12" aria-hidden="true"><path d="M3 1 L5 3.5 L4 5 Q5 7 7 8 L8.5 7 L11 9 L9.5 11 Q4 10.5 1 2.5 Z" fill="var(--white)"/></svg>
      <span>+1-555-014-2290</span>
      <svg width="13" height="11" viewBox="0 0 13 11" style="margin-left:8px" aria-hidden="true"><rect x="0.5" y="2" width="12" height="8.5" fill="none" stroke="var(--white)"/><path d="M0.5 2 L6.5 7 L12.5 2" fill="none" stroke="var(--white)"/></svg>
      <span>hello@meridiantrials.net</span>
    </div>
    <div>Meridian Trials Co. 52 Linden Avenue, Fairview, NY 10990</div>
  </div>

  <div class="brand front-brand">
    <span class="brand-dot"></span>
    <div class="brand-name"><span>MERIDIAN TRIALS</span><span>CO.</span></div>
  </div>

  <div class="web-address">www.<b>meridiantrials</b>.net</div>

  <div class="card card-left">
    <div class="card-brand"><span class="brand-dot"></span><span>MERIDIAN TRIALS CO.</span></div>
    <div class="card-contact">+1-555-014-2290<br>hello@meridiantrials.net</div>
    <div class="card-address">Meridian Trials Co. 52 Linden Avenue<br>Fairview, NY 10990</div>
    <div class="card-holder">Your Name<br>Title</div>
  </div>

  <div class="card card-right">
    <div class="card-brand"><span class="brand-dot"></span><span>MERIDIAN TRIALS CO.</span></div>
    <div class="card-contact">+1-555-014-2290<br>hello@meridiantrials.net</div>
    <div class="card-address">Meridian Trials Co. 52 Linden Avenue<br>Fairview, NY 10990</div>
    <div class="card-holder">Your Name<br>Title</div>
  </div>
</main>
</body>
</html>
```